Local Flower Farm Needs Business Card Design

I need business cards designed for a flower farm based in Eudora, Kansas.
Business Info:
We are a local cut flower farm located in Eudora, Kansas, founded by Corinne Haldwick. What started as a passion for agriculture and search for more joy in daily life has blossomed into a small business dedicated to providing the community with beautiful, fresh, and sustainable flowers. We specialize in local, seasonal blooms, ensuring that every petal reflects the care and dedication we pour into our craft. Our mission is to deliver the highest quality flowers directly to our customers through local farmers markets and to florists who share our commitment to sustainability. Join us in celebrating the beauty of nature, one bloom at a time!
Contact Details:
Corinne Haldwick
Owner
Phone 913-555-0147
Facebook: Rosalind Thorpe Gardens
Instagram: @RosalindThorpeGardens
Website: RosalindThorpeGardens.example
Target Market(s)
Wholesale to Florists and Direct to Consumer via Farmers Market
Industry/Entity Type
Florist, Farm
Contact Information for Business Card
Name, Contact Info, Logo
Look and feel
Each slider illustrates characteristics of the customer's brand and the style your logo design should communicate.

```html
<!DOCTYPE html>
<html lang="en">
<head>
<meta charset="UTF-8">
<title>Rosalind Thorpe Gardens – Business Card</title>
<link rel="stylesheet" href="https://fonts.googleapis.com/css2?family=Crimson+Text:wght@400;600;700&display=swap">
<style>
  :root {
    --ink: #1c3834;
    --ink-soft: #2a2f2e;
    --swoosh-grey: #c8cacb;
    --card: #ffffff;
    --backdrop: #dcdedf;
  }
  * { margin: 0; padding: 0; box-sizing: border-box; }
  html, body {
    width: 1200px; height: 813px; overflow: hidden;
    background: var(--backdrop);
    font-family: "Crimson Text", Georgia, serif;
    color: var(--ink-soft);
  }
  .stage { position: relative; width: 1200px; height: 813px; }
  .card {
    position: absolute; top: 246px;
    width: 560px; height: 320px;
    background: var(--card);
    border-radius: 18px;
    overflow: hidden;
  }
  .card--back { left: 27px; }
  .card--front { left: 613px; }

  .brand-seal {
    position: absolute;
    display: flex; align-items: center; justify-content: center;
    border: 2px solid var(--ink);
    border-radius: 50%;
    text-align: center;
    color: var(--ink);
    font-weight: 600;
    text-transform: uppercase;
    letter-spacing: 0.12em;
    line-height: 1.25;
  }
  .card--back .brand-seal { width: 230px; height: 230px; left: 165px; top: 45px; font-size: 24px; }
  .card--front .brand-seal { width: 180px; height: 180px; left: 340px; top: 30px; font-size: 19px; }

  .swoosh { position: absolute; inset: 0; width: 560px; height: 320px; }

  .divider {
    position: absolute; left: 296px; top: 42px;
    width: 2px; height: 168px; background: var(--ink);
  }

  .contact { position: absolute; left: 30px; top: 118px; }
  .contact__name { font-size: 21px; font-weight: 700; color: #1a1a1a; line-height: 1.1; }
  .contact__role { font-size: 14px; margin-bottom: 8px; }
  .contact__list { list-style: none; }
  .contact__item {
    display: flex; align-items: center; gap: 6px;
    font-size: 15.5px; line-height: 1.3; color: #1a1a1a;
  }
  .contact__icon { width: 12px; height: 12px; flex: none; }
</style>
</head>
<body>
<main class="stage">

  <section class="card card--back" aria-label="Card back">
    <div class="brand-seal">Rosalind<br>Thorpe<br>Gardens</div>
  </section>

  <section class="card card--front" aria-label="Card front">
    <svg class="swoosh" viewBox="0 0 560 320" aria-hidden="true">
      <path fill="var(--swoosh-grey)" d="M0,262 C150,296 300,236 420,206 C480,191 530,186 560,184 L560,320 L0,320 Z"/>
      <path fill="#ffffff" d="M0,280 C150,306 300,252 420,222 C480,208 530,203 560,201 L560,320 L0,320 Z"/>
      <path fill="var(--ink)" d="M0,292 C160,316 310,268 425,238 C485,224 530,218 560,216 L560,320 L0,320 Z"/>
    </svg>

    <div class="contact">
      <p class="contact__name">Corinne Haldwick</p>
      <p class="contact__role">Owner</p>
      <ul class="contact__list">
        <li class="contact__item">
          <svg class="contact__icon" viewBox="0 0 12 12" aria-hidden="true"><path fill="var(--ink-soft)" d="M1,4 Q6,0 11,4 L10,6 L8,5 L8,4 Q6,3 4,4 L4,5 L2,6 Z M2,7 H10 V11 H2 Z"/></svg>
          913-555-0147
        </li>
        <li class="contact__item">
          <svg class="contact__icon" viewBox="0 0 12 12" aria-hidden="true"><circle cx="6" cy="6" r="5.5" fill="var(--ink-soft)"/><path d="M0.5,6 H11.5 M6,0.5 V11.5 M6,0.5 Q2,6 6,11.5 M6,0.5 Q10,6 6,11.5" stroke="#fff" stroke-width="0.8" fill="none"/></svg>
          RosalindThorpeGardens.example
        </li>
        <li class="contact__item">
          <svg class="contact__icon" viewBox="0 0 12 12" aria-hidden="true"><circle cx="6" cy="6" r="5.5" fill="var(--ink-soft)"/></svg>
          Rosalind Thorpe Gardens
        </li>
        <li class="contact__item">
          <svg class="contact__icon" viewBox="0 0 12 12" aria-hidden="true"><rect x="0.5" y="0.5" width="11" height="11" rx="2" fill="var(--ink-soft)"/></svg>
          @RosalindThorpeGardens
        </li>
      </ul>
    </div>

    <div class="divider"></div>
    <div class="brand-seal">Rosalind<br>Thorpe<br>Gardens</div>
  </section>

</main>
</body>
</html>
```